New florist business website design

Number 1 want is an easy to navigate & check out website
Needs to be beautiful and eye catching as well.
This is an online only business (no shop front)
Rustic and blush pinks, neutrals, woods, leaves
Customers need to be able to go onto my website, select something they want to buy but have the option to use a drop down box to change colours of the flowers, or add notes to make changes to the arrangement

Industry/Entity Type

Florist

Coding

Coded - Design and coding required

Number of Pages Required

5+ page

Colors
f9d9e8
fff2ec
fffefc

Requirements
Must have
• Drop down menu to take you to other pages for Arrangements, bouquets, everlasting arrangements, gifts, contact
Be able to purchase and “add to basket”
Checkout page
Nice to have
• Be able to add my own photos once I’ve taken new ones
Should not have
• Tacky images or clip art

```html
<!DOCTYPE html>
<html lang="en">
<head>
<meta charset="utf-8">
<title>Petal &amp; Thorn — Florist</title>
<link href="https://fonts.googleapis.com/css2?family=Montserrat:wght@400;500;600&family=Arimo:ital,wght@0,400;1,400&display=swap" rel="stylesheet">
<style>
:root{
  --blush:#f5c9dd;
  --blush-soft:#f9d9e8;
  --peach:#fbe3cc;
  --cream:#fff2ec;
  --paper:#fffefc;
  --ink:#2a2a2a;
  --muted:#555;
  --line:#cfcfcf;
  --accent:#f08a2a;
  --footer:#2b2b2b;
  --head:'Montserrat',sans-serif;
  --body:'Arimo',Arial,sans-serif;
}
*{box-sizing:border-box;margin:0;padding:0}
html,body{width:1200px;height:3613px;overflow:hidden;background:var(--paper)}
body{position:relative;font-family:var(--body);color:var(--ink)}
.abs{position:absolute}
.btn{position:absolute;border:1.5px solid var(--ink);font-family:var(--head);font-weight:500;color:var(--ink);display:flex;align-items:center;justify-content:center;letter-spacing:.3px;background:transparent}

/* header + hero */
.hero{position:absolute;left:0;top:0;width:1200px;height:816px;background:var(--blush)}
.hero-photo{position:absolute;left:0;top:182px;width:700px;height:634px;background:radial-gradient(ellipse at 40% 35%,#f2a24a 0%,#e0456a 30%,#9bb24d 60%,rgba(245,201,221,0) 80%)}
.logo{position:absolute;left:112px;top:58px;width:180px;text-align:center;font-family:var(--head);font-weight:400;font-size:28px;color:#6b5562}
.logo small{display:block;font-size:10px;letter-spacing:2px;margin-bottom:4px}
.nav{position:absolute;top:78px;left:380px;display:flex;gap:34px;font-family:var(--head);font-weight:600;font-size:12.5px}
.cart{position:absolute;left:1028px;top:56px;width:60px;height:60px;border:1.5px solid var(--ink);border-radius:50%;display:flex;flex-direction:column;align-items:center;justify-content:center;font-size:11px}
.hero-title{position:absolute;left:603px;top:350px;width:520px;text-align:center;font-family:var(--head);font-weight:400;font-size:86px;color:var(--ink);letter-spacing:1px}
.hero-text{position:absolute;left:620px;top:482px;width:535px;text-align:center;font-size:18.5px;line-height:32px;color:#333}

/* offers */
.offer{position:absolute;top:850px;width:313px;height:240px;font-family:var(--head)}
.offer .t{position:absolute;font-size:21px;font-weight:500}
.offer .s{position:absolute;font-size:15px;font-weight:500}

/* products */
.sec-title{position:absolute;font-family:var(--head);font-weight:500;font-size:22px;letter-spacing:.3px}
.arrow{position:absolute;top:1146px;width:38px;height:36px;background:#ddd;border-radius:3px;display:flex;align-items:center;justify-content:center}
.product{position:absolute;width:235px;text-align:center;font-family:var(--head)}
.product .img{width:235px;height:259px;background:var(--cream)}
.product .img div{width:150px;height:190px;margin:35px auto 0;border-radius:50% 50% 40% 40%}
.product .name{margin-top:22px;font-size:17px;font-weight:500}
.product .price{margin-top:8px;font-size:17px;color:#444}

/* deal */
.deal{position:absolute;left:0;top:1984px;width:1200px;height:627px;background:var(--peach)}
.basket{position:absolute;left:84px;top:98px;width:505px;height:486px;background:radial-gradient(ellipse at 50% 38%,#e2427a 0%,#d6376e 35%,#b9733f 62%,rgba(251,227,204,0) 75%)}
.count{position:absolute;top:377px;width:78px;height:62px;background:#fff;border:1px solid #ccc;text-align:center;font-family:var(--head)}
.count b{display:block;font-weight:500;font-size:26px;margin-top:6px;color:#333}
.count span{font-size:13px;color:#555}

/* reviews */
.review{position:absolute;top:2760px;width:311px;height:392px;background:#fff;box-shadow:0 0 10px rgba(0,0,0,.12);text-align:center}
.avatar{width:140px;height:140px;border-radius:50%;margin:24px auto 0;background:linear-gradient(#9b8b80,#5a4a42)}
.review h4{font-family:var(--head);font-weight:500;font-size:17px;margin-top:27px}
.stars{color:var(--accent);font-size:14px;letter-spacing:2px;margin-top:6px}
.review p{font-style:italic;font-size:13.5px;line-height:23px;color:#444;margin:14px 24px 0}

/* footer */
.footer{position:absolute;left:0;top:3220px;width:1200px;height:393px;background:var(--footer);color:#fff}
.f-title{position:absolute;top:62px;font-family:var(--head);font-weight:500;font-size:21px}
.f-links{position:absolute;left:453px;top:106px;list-style:none;font-size:15px;line-height:30px}
.f-links li::before{content:"»";margin-right:18px}
.f-text{position:absolute;font-size:13.5px;line-height:22px}
.card{position:absolute;top:239px;width:50px;height:36px;background:#fff;border-radius:3px}
</style>
</head>
<body>

<header class="hero">
  <div class="hero-photo" role="img" aria-label="Bouquet of colourful tulips tied with a lilac ribbon"></div>
  <div class="logo"><small>fresh and everlasting flowers</small>Petal &amp; Thorn</div>
  <nav class="nav"><span>ARRANGEMENTS</span><span>BOUQUETS</span><span>EVERLASTING ARRANGEMENTS</span><span>GIFTS</span><span>CONTACT</span></nav>
  <div class="cart"><span>0</span>
    <svg width="16" height="14" viewBox="0 0 16 14"><path d="M0 1h3l2 8h8l2-6H4" fill="none" stroke="#2a2a2a" stroke-width="1.6"/><circle cx="6" cy="12" r="1.4"/><circle cx="12" cy="12" r="1.4"/></svg>
  </div>
  <h1 class="hero-title">Petal&amp;Thorn</h1>
  <p class="hero-text">Sed ut perspiciatis unde omnis iste natus error sit voluptatem accusantium doloremque laudantium</p>
  <div class="btn" style="left:809px;top:566px;width:156px;height:58px;font-size:16px">SHOP NOW</div>
</header>

<section>
  <div class="offer" style="left:112px;background:linear-gradient(90deg,#f0cfe0,#f6d3e0)" role="img" aria-label="Pink tulips beside a wrapped gift">
    <div class="t" style="right:22px;top:40px">30% OFFER</div>
    <div class="s" style="right:22px;top:70px">GIFTS FLOWERS</div>
    <div class="btn" style="left:191px;top:102px;width:101px;height:38px;font-size:12.5px">SHOP NOW</div>
  </div>
  <div class="offer" style="left:443px;background:linear-gradient(135deg,#f1efec,#e5e1dc)" role="img" aria-label="Kraft paper gifts and roses on white wood">
    <div class="s" style="left:0;width:313px;text-align:center;top:90px">ARRANGEMENTS</div>
    <div class="t" style="left:0;width:313px;text-align:center;top:114px;font-size:25px">25% OFFERS</div>
  </div>
  <div class="offer" style="left:775px;background:linear-gradient(135deg,#ebe4d8,#d8ccbc)" role="img" aria-label="Peach roses with pink gift boxes">
    <div class="t" style="right:24px;top:27px">20% OFFER</div>
    <div class="s" style="right:24px;top:56px">BOUQUETS FLOWERS</div>
    <div class="btn" style="left:189px;top:90px;width:100px;height:38px;font-size:12.5px">SHOP NOW</div>
  </div>
</section>

<section>
  <h2 class="sec-title" style="left:112px;top:1151px">FEATURED PRODUCTS</h2>
  <div class="arrow" style="left:1010px"><svg width="10" height="12"><path d="M7 1L2 6l5 5" fill="none" stroke="#333" stroke-width="1.6"/></svg></div>
  <div class="arrow" style="left:1051px"><svg width="10" height="12"><path d="M3 1l5 5-5 5" fill="none" stroke="#333" stroke-width="1.6"/></svg></div>

  <div class="product" style="left:112px;top:1217px"><div class="img"><div role="img" aria-label="Coral rose bouquet in pink wrap" style="background:radial-gradient(#ef7a74,#8ca872 70%,transparent 72%)"></div></div><div class="name">PRODUCT NAME</div><div class="price">$25.00</div></div>
  <div class="product" style="left:359px;top:1217px"><div class="img"><div role="img" aria-label="Cream and pink mixed bouquet" style="background:radial-gradient(#f1ecd0,#5d7f44 70%,transparent 72%)"></div></div><div class="name">PRODUCT NAME</div><div class="price">$25.00</div></div>
  <div class="product" style="left:606px;top:1217px"><div class="img"><div role="img" aria-label="Purple iris bouquet" style="background:radial-gradient(#6c55c8,#5b8a4c 70%,transparent 72%)"></div></div><div class="name">PRODUCT NAME</div><div class="price">$25.00</div></div>
  <div class="product" style="left:854px;top:1217px"><div class="img"><div role="img" aria-label="Autumn leaf wreath" style="background:radial-gradient(transparent 45%,#c88a4a 50%,transparent 72%)"></div></div><div class="name">PRODUCT NAME</div><div class="price">$25.00</div></div>

  <div class="product" style="left:112px;top:1586px"><div class="img"><div role="img" aria-label="Dried flower bouquet" style="background:radial-gradient(#d9b99a,#a77f5c 70%,transparent 72%)"></div></div><div class="name">PRODUCT NAME</div><div class="price">$25.00</div></div>
  <div class="product" style="left:359px;top:1586px"><div class="img"><div role="img" aria-label="Gerbera bouquet" style="background:radial-gradient(#f6b730,#e05b2b 40%,#3f7a36 70%,transparent 72%)"></div></div><div class="name">PRODUCT NAME</div><div class="price">$25.00</div></div>
  <div class="product" style="left:606px;top:1586px"><div class="img"><div role="img" aria-label="Pink tulips in paper wrap" style="background:radial-gradient(#e23570,#e8d8c2 70%,transparent 72%)"></div></div><div class="name">PRODUCT NAME</div><div class="price">$25.00</div></div>
  <div class="product" style="left:854px;top:1586px"><div class="img"><div role="img" aria-label="Tulips in a glass vase" style="background:radial-gradient(#ee6f9a,#5a9a4a 70%,transparent 72%)"></div></div><div class="name">PRODUCT NAME</div><div class="price">$25.00</div></div>
</section>

<section class="deal">
  <div class="basket" role="img" aria-label="Wicker basket filled with pink roses"></div>
  <h2 class="abs" style="left:600px;width:500px;top:152px;text-align:center;font-family:var(--head);font-weight:500;font-size:37px">PETAL THORN</h2>
  <p class="abs" style="left:600px;width:500px;top:212px;text-align:center;font-family:var(--head);font-size:32px">Hot Deal! Sale Up to 20% off</p>
  <p class="abs" style="left:612px;width:476px;top:270px;text-align:center;font-size:15px;line-height:25.5px;color:#555">Sed ut perspiciatis unde omnis iste natus error sit voluptatem accusa ntium doloremque laudantium, totam rem aperiam, eaque ipsa arc hitecto beatae vitae dicta sunt explicabo.</p>
  <div class="count" style="left:679px"><b>10</b><span>DAYS</span></div>
  <div class="count" style="left:766px"><b>22</b><span>HOURS</span></div>
  <div class="count" style="left:853px"><b>05</b><span>MINTS</span></div>
  <div class="count" style="left:943px"><b>25</b><span>SEC</span></div>
  <div class="btn" style="left:777px;top:465px;width:147px;height:49px;font-size:15.5px">SHOP NOW</div>
</section>

<section>
  <h2 class="sec-title" style="left:0;width:1200px;text-align:center;top:2667px;font-size:25px">CUSTOMER REVIEWS</h2>
  <div class="abs" style="left:573px;top:2712px;width:54px;height:2px;background:#f2c9a8"></div>
  <div class="review" style="left:112px"><div class="avatar" role="img" aria-label="Customer portrait"></div><h4>JHON SMITH</h4><div class="stars">★★★★★</div><p>Neque porro quisquam est, qui dolorem ipsum quia dolor sit amet, consectetur, adi pisci velit, sed quia non numquam eius modi tempora incidunt ut labore et dolore aliquam quaerat voluptatem.</p></div>
  <div class="review" style="left:444px"><div class="avatar" role="img" aria-label="Customer portrait"></div><h4>JHON SMITH</h4><div class="stars">★★★★★</div><p>Neque porro quisquam est, qui dolorem ipsum quia dolor sit amet, consectetur, adi pisci velit, sed quia non numquam eius modi tempora incidunt ut labore et dolore aliquam quaerat voluptatem.</p></div>
  <div class="review" style="left:777px"><div class="avatar" role="img" aria-label="Customer portrait"></div><h4>JHON SMITH</h4><div class="stars">★★★★★</div><p>Neque porro quisquam est, qui dolorem ipsum quia dolor sit amet, consectetur, adi pisci velit, sed quia non numquam eius modi tempora incidunt ut labore et dolore aliquam quaerat voluptatem.</p></div>
</section>

<footer class="footer">
  <div class="abs" style="left:119px;top:80px;width:246px;text-align:center;font-family:var(--head);font-size:34px">Petal &amp; Thorn</div>
  <div class="card" style="left:112px"></div>
  <div class="card" style="left:167px"></div>
  <div class="card" style="left:222px"></div>
  <div class="card" style="left:277px"></div>
  <div class="card" style="left:332px"></div>

  <h3 class="f-title" style="left:453px">LINKS</h3>
  <ul class="f-links"><li>Home</li><li>Arrangements</li><li>Bouquets</li><li>Everlasting</li><li>Gifts</li><li>Contact</li></ul>

  <h3 class="f-title" style="left:642px">GET IN TOUCH</h3>
  <p class="f-text" style="left:645px;top:110px">Tele : 000.123.1231</p>
  <p class="f-text" style="left:645px;top:139px">2050 Lorem Ipsum Dummy<br>Lorem CA 95110</p>
  <p class="f-text" style="left:645px;top:190px">info@petalthorn.com</p>

  <h3 class="f-title" style="left:862px">NEWSLETTER</h3>
  <p class="f-text" style="left:862px;top:110px;width:240px">Sed ut perspiciatis unde error sit vol uptatem accusantium...</p>
  <div class="abs" style="left:862px;top:173px;width:226px;height:42px;background:#fff;color:#333;font-size:13.5px;padding:13px 14px">Enter Email Id :</div>
  <div class="abs" style="left:862px;top:226px;width:98px;height:34px;background:var(--peach);color:#333;font-family:var(--head);font-weight:600;font-size:12px;display:flex;align-items:center;justify-content:center">SUBMIT</div>

  <p class="abs" style="left:0;width:1200px;text-align:center;top:341px;font-size:15px">© Copyright 2021.Petal Thorn.All Rights Reserved</p>
</footer>

</body>
</html>
```